Veldmark Supplies Business Card

Professional business card that stand out to our potential customers. Front and back with clean modern design

Industry/Entity Type

Oil and gas

Contact Information for Business Card

Name, address, website , office phone and cell number

Requirements
Must have
• Editable files for each employee

```html
<!DOCTYPE html>
<html lang="en">
<head>
<meta charset="utf-8">
<title>Veldmark Supplies Business Card</title>
<link rel="stylesheet" href="https://fonts.googleapis.com/css2?family=Montserrat:wght@500;700;800&display=swap">
<style>
  :root {
    --brand-red: #ec2227;
    --brand-blue: #0bafd1;
    --paper: #ffffff;
    --backdrop: #2e2e2e;
    --card-w: 540px;
    --card-h: 309px;
  }
  * { box-sizing: border-box; margin: 0; padding: 0; }
  html, body { width: 1200px; height: 689px; overflow: hidden; }
  body {
    background: var(--backdrop);
    font-family: "Montserrat", sans-serif;
    display: flex;
    align-items: center;
    justify-content: center;
    gap: 40px;
  }
  .card {
    position: relative;
    width: var(--card-w);
    height: var(--card-h);
    border-radius: 18px;
    overflow: hidden;
  }
  /* Front */
  .card-front {
    background: var(--brand-red);
    display: flex;
    align-items: center;
    justify-content: center;
  }
  .wordmark {
    display: flex;
    align-items: center;
    gap: 12px;
    font-weight: 800;
    text-transform: uppercase;
    letter-spacing: 0.06em;
  }
  .wordmark-square { width: 20px; height: 20px; }
  .card-front .wordmark { color: var(--paper); font-size: 30px; }
  .card-front .wordmark-square { background: var(--paper); }
  /* Back */
  .card-back { background: var(--paper); }
  .wave { position: absolute; inset: 0; width: 100%; height: 100%; }
  .card-back .wordmark {
    position: absolute;
    left: 36px;
    top: 110px;
    color: var(--brand-red);
    font-size: 19px;
    gap: 9px;
  }
  .card-back .wordmark-square { width: 14px; height: 14px; background: var(--brand-blue); }
  .contact {
    position: absolute;
    right: 26px;
    top: 98px;
    color: var(--paper);
    text-align: right;
    font-size: 11.5px;
    font-weight: 500;
    line-height: 1.45;
  }
  .contact-name { font-weight: 800; font-size: 13px; text-transform: uppercase; letter-spacing: 0.02em; }
  .contact-title { margin-bottom: 10px; }
  .contact-address { margin-bottom: 8px; }
  .contact-line { display: flex; align-items: center; justify-content: flex-end; gap: 8px; height: 19px; }
  .icon { width: 14px; height: 14px; flex: none; }
</style>
</head>
<body>

<section class="card card-front" aria-label="Card front">
  <div class="wordmark"><span class="wordmark-square"></span>Veldmark Supplies</div>
</section>

<section class="card card-back" aria-label="Card back">
  <svg class="wave" viewBox="0 0 540 309" preserveAspectRatio="none" aria-hidden="true">
    <path d="M0,262 C170,228 250,190 300,105 C345,30 420,8 470,0" fill="none" stroke="var(--brand-red)" stroke-width="3"/>
    <path d="M0,285 C180,250 265,205 315,115 C355,42 430,18 500,0 L515,0 C440,22 372,55 330,128 C280,215 190,262 0,298 Z" fill="var(--brand-blue)"/>
    <path d="M0,309 L0,300 C195,262 285,215 335,130 C378,58 450,26 540,8 L540,309 Z" fill="var(--brand-red)"/>
  </svg>

  <div class="wordmark"><span class="wordmark-square"></span>Veldmark Supplies</div>

  <div class="contact">
    <p class="contact-name">Dorian Kessler</p>
    <p class="contact-title">President</p>
    <p class="contact-address">482 Quarry Lane, Ste 210<br>Harlow, TX 79104</p>
    <p class="contact-line">555-014-2236
      <svg class="icon" viewBox="0 0 14 14" aria-hidden="true"><rect width="14" height="14" fill="var(--brand-blue)"/><path d="M3,9 Q3,5 7,5 Q11,5 11,9 L9,9 L9,7.5 L5,7.5 L5,9 Z" fill="#fff"/></svg></p>
    <p class="contact-line">555-018-7741
      <svg class="icon" viewBox="0 0 14 14" aria-hidden="true"><rect width="14" height="14" fill="var(--brand-blue)"/><rect x="4.5" y="2.5" width="5" height="9" rx="1" fill="none" stroke="#fff" stroke-width="1.2"/></svg></p>
    <p class="contact-line">info@veldmarksupplies.com
      <svg class="icon" viewBox="0 0 14 14" aria-hidden="true"><rect width="14" height="14" fill="var(--brand-blue)"/><rect x="2.5" y="4" width="9" height="6" fill="none" stroke="#fff" stroke-width="1.1"/><path d="M2.5,4 L7,7.5 L11.5,4" fill="none" stroke="#fff" stroke-width="1.1"/></svg></p>
    <p class="contact-line">www.veldmarksupplies.com
      <svg class="icon" viewBox="0 0 14 14" aria-hidden="true"><rect width="14" height="14" fill="var(--brand-blue)"/><circle cx="7" cy="7" r="4" fill="none" stroke="#fff" stroke-width="1.1"/><path d="M3,7 H11 M7,3 Q9.5,7 7,11 Q4.5,7 7,3" fill="none" stroke="#fff" stroke-width="0.9"/></svg></p>
  </div>
</section>

</body>
</html>
```